Micro Markets Vending business needs a web design

I purchased a logo through MarkHarbor and asked them to design my website but was told they couldn't and that I needed to contact you.
I was building a website through Plume using AI and liked what they had created verbiage-wise but I can't figure out how to finish it the way I would like it. Will send screen shots of what was written, and subsequently used in my slogan under my logo. Would like to use the colors in my logo for my website.
About the company:
RT Snackworks, LLC offers micro market vending machines. Swipe your card, open the doors, take what you want. Can be customized by size for the space, and items for sale within the machines. Pictures of the machines are attached as examples.
I don't need a Testimonials page right now since we are a new company, but will need to add one at some point.
I also like the idea of a contact us button, as shown in the last picture (although it says subscribe). We do not have any emails set up as of yet. Haven't figured out how to do that, but will.
Just let me know what files you need from MarkHarbor for my logo.
Target Market(s)
Apartment complexes, Buildings, Hotels, Gyms, etc
Industry/Entity Type
Vending Machines
Coding
Coded - Design and coding required
Number of Pages Required
1 page
Font styles to use
Other font styles liked:
- Your choice on font style that complements our logo font.
Look and feel
Each slider illustrates characteristics of the customer's brand and the style your logo design should communicate.

```html
<!DOCTYPE html>
<html lang="en">
<head>
<meta charset="utf-8">
<title>RT Snackworks, LLC – Micro Market Vending</title>
<link rel="stylesheet" href="https://fonts.googleapis.com/css2?family=Poppins:ital,wght@0,400;0,500;0,600;0,700;0,800;1,400;1,500&display=swap">
<style>
:root{
  --green:#3e9b35;
  --green-dark:#2c7a27;
  --green-light:#5fb347;
  --ink:#0f2410;
  --text:#333;
  --grey-band:#eeeeee;
  --footer:#0e1a0f;
  --white:#fff;
}
*{box-sizing:border-box;margin:0;padding:0}
html,body{width:1200px;height:2526px;overflow:hidden}
body{font-family:"Poppins",sans-serif;color:var(--text);background:var(--white);position:relative}
section,header,footer{position:absolute;left:0;width:1200px}

/* header */
.site-header{top:0;height:116px;background:var(--white)}
.brand{position:absolute;left:76px;top:30px;display:flex;flex-direction:column;align-items:center;width:180px}
.brand-mark{width:40px;height:40px;background:var(--green-light);border-radius:4px;margin-bottom:6px}
.brand-name{font-weight:700;font-size:15px;color:var(--ink);letter-spacing:.5px;white-space:nowrap}
.brand-tagline{font-size:5px;color:var(--green);letter-spacing:1.6px;text-transform:uppercase;margin-top:2px;white-space:nowrap}
.main-nav{position:absolute;right:50px;top:52px;display:flex;gap:40px}
.main-nav a{font-size:12.5px;font-weight:600;color:#222;text-decoration:none;letter-spacing:.3px}
.main-nav a.active{color:var(--green);border-bottom:2px solid var(--green);padding-bottom:2px}

/* hero */
.hero{top:116px;height:604px}
.hero-photo{position:absolute;inset:0;background:linear-gradient(180deg,#3a3d40 0%,#4a4a48 35%,#5b5650 60%,#2c2b2a 100%)}
.hero-content{position:absolute;left:0;right:0;top:196px;text-align:center;color:var(--white)}
.hero-title{font-size:56px;font-weight:800;letter-spacing:1px;line-height:1}
.hero-lead{margin:18px auto 0;width:880px;font-size:13.8px;font-weight:700;line-height:25px;text-transform:uppercase}
.btn{display:inline-block;background:linear-gradient(180deg,var(--green-light),var(--green-dark));color:var(--white);font-weight:600;font-size:16px;border-radius:24px;text-decoration:none;text-align:center}
.hero .btn{margin-top:18px;width:152px;height:47px;line-height:47px}
.hero-dots{position:absolute;top:558px;left:0;right:0;display:flex;justify-content:center;gap:10px}
.hero-dots span{width:7px;height:7px;border-radius:50%;background:var(--white)}
.hero-dots span.on{background:var(--green-light)}

/* about */
.about{top:782px;height:314px}
.about-photo{position:absolute;left:0;top:0;width:588px;height:313px;border-radius:0 157px 157px 0;background:linear-gradient(135deg,#2a3b52,#4c4a45 55%,#1f2226)}
.about-body{position:absolute;left:615px;top:10px;width:520px}
h2{font-size:28px;font-weight:700;color:var(--ink);letter-spacing:.5px}
.about-body p{font-size:14px;line-height:27px;margin-top:14px;color:#333}
.about-body p + p{margin-top:8px}
.about .btn{margin-top:22px;width:152px;height:47px;line-height:47px}

/* why */
.why{top:1170px;height:627px;background:var(--grey-band)}
.why-body{position:absolute;left:75px;top:76px;width:580px}
.intro{font-style:italic;font-weight:500;color:var(--green);font-size:17px;line-height:27px;margin-top:12px}
.feature{display:flex;gap:22px;margin-top:28px}
.feature:first-of-type{margin-top:26px}
.feature-icon{flex:none;width:70px;height:70px;border-radius:50%;background:var(--green);display:flex;align-items:center;justify-content:center}
.feature-icon.outline{background:var(--white);border:1.5px solid var(--green)}
.feature h3{font-size:19px;font-weight:600;color:var(--ink);margin-top:-6px}
.feature p{font-size:13.4px;line-height:21.5px;margin-top:4px}
.why-photo{position:absolute;left:746px;top:52px;width:380px;height:526px;border-radius:6px;background:linear-gradient(180deg,#1c1c1c,#3b4a55 40%,#2a2a2a 85%,#111)}

/* contact */
.contact{top:1860px;height:515px}
.contact-photo{position:absolute;left:76px;top:2px;width:512px;height:510px;border-radius:50% 50% 50% 50%/48% 48% 52% 52%;background:linear-gradient(180deg,#7a4b3a,#2d3a48 35%,#1f2530 75%,#6b5a4c)}
.contact-body{position:absolute;left:618px;top:22px;width:510px}
.contact-form{margin-top:24px;display:grid;grid-template-columns:1fr 1fr;gap:12px 13px}
.field{height:50px;border:1px solid #b8b8b8;border-radius:25px;padding:0 20px;font-size:12.5px;color:#333;display:flex;align-items:center}
.field.message{grid-column:1/3;height:108px;align-items:flex-start;padding-top:20px;border-radius:30px}
.contact .btn{margin-top:12px;width:152px;height:47px;line-height:47px;grid-column:1}

/* footer */
.site-footer{top:2441px;height:85px;background:var(--footer);color:var(--white)}
.copyright{position:absolute;left:74px;top:36px;font-size:13px}
.social{position:absolute;right:68px;top:28px;display:flex;gap:18px}
.social span{width:24px;height:24px;border-radius:50%;background:var(--white)}
.social span:nth-child(2){background:var(--green-light)}
</style>
</head>
<body>

<header class="site-header">
  <div class="brand">
    <div class="brand-mark"></div>
    <div class="brand-name">RT SNACKWORKS, LLC</div>
    <div class="brand-tagline">where convenience meets customization</div>
  </div>
  <nav class="main-nav">
    <a href="#" class="active">HOME</a>
    <a href="#">ABOUT US</a>
    <a href="#">PRODUCTS</a>
    <a href="#">WHY US</a>
    <a href="#">CONTACT US</a>
  </nav>
</header>

<section class="hero">
  <div class="hero-photo" role="img" aria-label="Micro market with refrigerated drink coolers and snack shelves"></div>
  <div class="hero-content">
    <h1 class="hero-title">DISCOVER OUR RANGE</h1>
    <p class="hero-lead">Welcome to RT Snackworks, where convenience meets customization. Our micro market vending machines in Greater Houston, TX, offer a variety of snacks and drinks tailored to your preferences. Swipe your credit card, open the doors, and indulge in what you desire.</p>
    <a href="#" class="btn">Explore Now</a>
  </div>
  <div class="hero-dots"><span class="on"></span><span></span><span></span><span></span></div>
</section>

<section class="about">
  <div class="about-photo" role="img" aria-label="Snack rack and drink cooler installed in an office lounge"></div>
  <div class="about-body">
    <h2>ABOUT RT SNACKWORKS, LLC</h2>
    <p>At RT Snackworks, we are dedicated to revolutionizing the vending experience.&nbsp; Our mission is to provide a convenient way for you to access your favorite snacks and drinks in a hassle-free manner.</p>
    <p>With a focus on customer satisfaction, we ensure that our products are always fresh and our machines are well-maintained. Experience the future of vending with RT Snackworks, LLC.</p>
    <a href="#" class="btn">Explore Now</a>
  </div>
</section>

<section class="why">
  <div class="why-body">
    <h2>WHY CHOOSE US</h2>
    <p class="intro">RT Snackworks stands out for its commitment to quality, convenience, and customization. We prioritize customer preferences and aim to provide a seamless vending experience.</p>
    <div class="feature">
      <div class="feature-icon"><svg width="26" height="26" viewBox="0 0 24 24" fill="#fff"><path d="M2 10h4v11H2zM8 21h9.5a2 2 0 0 0 2-1.6l1.4-7A2 2 0 0 0 19 10h-5l.9-4.3A1.8 1.8 0 0 0 11.8 4L8 10z"/></svg></div>
      <div><h3>Quality Products</h3><p>Our vending machines are stocked with a diverse range of snacks and drinks, ensuring that there's something for everyone. We source only the freshest products for your enjoyment.</p></div>
    </div>
    <div class="feature">
      <div class="feature-icon outline"><svg width="24" height="24" viewBox="0 0 24 24" fill="none" stroke="#3e9b35" stroke-width="2"><circle cx="12" cy="12" r="9"/><path d="M12 7v5l3 2"/></svg></div>
      <div><h3>Convenience</h3><p>Our vending machines are stocked with a diverse range of snacks and drinks, ensuring that there's something for everyone. We source only the freshest products for your enjoyment.</p></div>
    </div>
    <div class="feature">
      <div class="feature-icon"><svg width="28" height="28" viewBox="0 0 24 24" fill="none" stroke="#fff" stroke-width="2"><path d="M3 6h18M3 12h18M3 18h18"/><circle cx="15" cy="6" r="1.6" fill="#fff"/><circle cx="8" cy="12" r="1.6" fill="#fff"/><circle cx="14" cy="18" r="1.6" fill="#fff"/></svg></div>
      <div><h3>Customization</h3><p>Our vending machines are stocked with a diverse range of snacks and drinks, ensuring that there's something for everyone. We source only the freshest products for your enjoyment.</p></div>
    </div>
  </div>
  <div class="why-photo" role="img" aria-label="Two black glass-door micro market coolers stocked with drinks"></div>
</section>

<section class="contact">
  <div class="contact-photo" role="img" aria-label="Double-door micro market cooler with snacks and drinks against a brick wall"></div>
  <div class="contact-body">
    <h2>CONTACT US</h2>
    <p class="intro">RT Snackworks stands out for its commitment to quality, convenience, and customization. We prioritize customer preferences and aim to provide a seamless vending experience.</p>
    <form class="contact-form">
      <div class="field">Name</div>
      <div class="field">Email Address</div>
      <div class="field">Phone No</div>
      <div class="field">Subject</div>
      <div class="field message">Message</div>
      <a href="#" class="btn">Submit</a>
    </form>
  </div>
</section>

<footer class="site-footer">
  <p class="copyright">Copyright © 2024, CompanyName. All Rights Reserved.</p>
  <div class="social"><span></span><span></span><span></span><span></span><span></span></div>
</footer>

</body>
</html>
```